interior designer/stylist looking for a letter press business card to reflect the stylish work

Hello Designers,
I need a business card design for an company called Mosaic Interior Design. I'm aiming at the high end residential and private client market in London providing sleek simple interiors. I'd like my business card to be pinterest worthy and expensive looking, i want people to pin it and for it to have a sought after look, and want prospective customers to hire me as their interior designer as my card is so beautiful.
I love letter press design. I also like the use of colour/foil on the edge.
Colour combos & general things I like -
Black and White
Navy Blue and Gold
Neutral colours (muted palette of greys whites navys beiges)
White Marble & brass
Vorelle (fashion designer)
....also open to other suggestions....
Please dont take the pink in the attached photos too literally. i'd like the card to look more masculine than feminine.
I'd like Mosaic on one side in one font, with interior design underneath so one word will make the statement....... unless anyone has any other ideas, open to suggestions.
I'd like a really simple font and for the whole card to look very graphic.
my details -
Petra Wendlecombe
Interior Designer & Stylist
email petra@mosaicinteriordesign.co.uk
phone +447311584209
website wwww.mosaicinteriordesign.co.uk
GO GO GO!! EXCITED TO SEE THE OUTCOME!!
x P
Target Market(s)
High End Residential and private clients
Industry/Entity Type
Business
Contact Information for Business Card
Mosaic Interior Design & Styling
Petra Wendlecombe
phone +447311584209

```html
<!DOCTYPE html>
<html lang="en">
<head>
<meta charset="UTF-8">
<title>Petra Wendlecombe — Interior Designer &amp; Stylist</title>
<link rel="stylesheet" href="https://fonts.googleapis.com/css2?family=Jost:wght@300&family=Open+Sans:wght@400&display=swap">
<style>
  :root {
    --copper-light: #e3a57c;
    --copper-mid: #d08a5c;
    --copper-dark: #b8703f;
    --card-white: #ffffff;
    --ink: #3a3a3a;
    --ink-soft: #444444;
  }
  html, body {
    margin: 0;
    padding: 0;
    width: 1200px;
    height: 686px;
    overflow: hidden;
    background: var(--card-white);
  }
  .business-card {
    position: relative;
    width: 1200px;
    height: 686px;
    box-sizing: border-box;
    background: linear-gradient(135deg, var(--copper-light) 0%, var(--copper-mid) 45%, var(--copper-dark) 70%, var(--copper-mid) 100%);
    padding: 14px 14px 12px 14px;
  }
  .card-face {
    position: relative;
    width: 100%;
    height: 100%;
    background: var(--card-white);
    text-align: center;
    color: var(--ink);
  }
  .designer-name {
    position: absolute;
    left: 0;
    right: 0;
    top: 198px;
    margin: 0;
    font-family: "Jost", sans-serif;
    font-weight: 300;
    font-size: 78px;
    line-height: 1;
    letter-spacing: 0.04em;
    color: var(--ink);
  }
  .designer-role {
    position: absolute;
    left: 0;
    right: 0;
    top: 306px;
    margin: 0;
    font-family: "Jost", sans-serif;
    font-weight: 300;
    font-size: 22px;
    line-height: 1;
    letter-spacing: 0.42em;
    color: var(--ink-soft);
  }
  .contact-list {
    position: absolute;
    left: 0;
    right: 0;
    top: 402px;
    margin: 0;
    padding: 0;
    list-style: none;
    font-family: "Open Sans", sans-serif;
    font-weight: 400;
    font-size: 24px;
    color: var(--ink);
  }
  .contact-item {
    height: 45px;
    line-height: 45px;
  }
</style>
</head>
<body>
  <div class="business-card">
    <div class="card-face">
      <h1 class="designer-name">PETRA WENDLECOMBE</h1>
      <p class="designer-role">INTERIOR DESIGNER &amp; STYLIST</p>
      <ul class="contact-list">
        <li class="contact-item">PETRA@MOSAICINTERIORDESIGN.CO.UK</li>
        <li class="contact-item">+447311584209</li>
        <li class="contact-item">WWW.MOSAICINTERIORDESIGN.CO.UK</li>
      </ul>
    </div>
  </div>
</body>
</html>
```